Diverse, up-scale salon needs eye-catching, unique business cards.

We are looking for a unique business card design for our stylist but that can also be multi functional and used for appointment reminder and referrals. I will need a design in a format that I can modify names and titles going forward. In the past we have had a dark background with the logo on one side, and stylist and contact information on the other but we are open to all ideas. I have included our mission statement as well as branded colors below. The statement doesn't need to go on the card, it's just a reference for target market. We need space for the stylists name, title, instagram handle and then the salons phone number, website and address. I am also open to adding a spot for a qr code linked to the stylist instagram or the salon booking link.

primary brand colors:
#333333 #233415 #36502a #93874a #000000
Mission statement:
Vessolin Hair Studio, a high-end salon located in the lively Downtown Farmington, Michigan, is committed to providing exceptional services in a welcoming and relaxed environment to meet the needs of our diverse clientele.
Our salon specializes in contemporary custom haircuts, coloring, extensions, and barbering and beard grooming services. Our team of skilled stylists is passionate and inventive in their hair styling techniques. At the heart of our salon are values centered on quality, innovation, creativity, and above all, comfort. These core values are evident in every appointment across our customizable array of services.
Our goal is to establish a benchmark for exceptional hair care for every human.
Website: www.vessolinhairstudio.example
instagram: @vessolinhairstudio
address: 41782 Pelham Crest Rd, Farmington MI
phone: 248-613-4087

Industry/Entity Type

Hair Salon

Contact Information for Business Card

Stylist name, title, phone, instagram, website, address, (optional qr code)

Requirements
Should not have
• Does not need mission statement on the card.

```html
<!DOCTYPE html>
<html lang="en">
<head>
<meta charset="utf-8">
<title>Vessolin Hair Studio – Business Card</title>
<link href="https://fonts.googleapis.com/css2?family=Arimo:wght@400;700&display=swap" rel="stylesheet">
<style>
  :root {
    --stage: #161616;
    --card-light: #ffffff;
    --card-dark: #000000;
    --ink: #000000;
    --muted: #808080;
    --paper: #ffffff;
  }
  * { box-sizing: border-box; margin: 0; padding: 0; }
  html, body { width: 1200px; height: 1059px; overflow: hidden; }
  body { background: var(--stage); position: relative; font-family: "Arimo", Arial, sans-serif; }

  .card { position: absolute; overflow: hidden; }
  .card--front { left: 258px; top: 89px; width: 689px; height: 394px; background: var(--card-light); }
  .card--back  { left: 252px; top: 541px; width: 701px; height: 400px; background: var(--card-dark); }

  .card__bands { position: absolute; inset: 0; }

  .brand-seal { position: absolute; display: flex; align-items: center; justify-content: center; text-align: center;
                border-radius: 50%; font-weight: 700; font-size: 19px; line-height: 1.25; letter-spacing: 1px; text-transform: uppercase; }
  .card--front .brand-seal { left: 60px; top: 67px; width: 252px; height: 252px; background: var(--paper);
                             border: 3px solid var(--ink); color: var(--ink); }
  .card--back .brand-seal { left: 391px; top: 74px; width: 252px; height: 252px;
                            border: 3px solid var(--paper); color: var(--paper); }

  .stylist { position: absolute; left: 348px; top: 55px; }
  .stylist__name { font-size: 21px; font-weight: 700; color: var(--ink); letter-spacing: 0.2px; }
  .stylist__title { font-size: 18px; color: var(--muted); margin-top: 1px; }

  .contact-list { position: absolute; left: 348px; top: 155px; list-style: none; }
  .contact-list li { display: flex; align-items: center; height: 28px; font-size: 19px; color: var(--muted); }
  .contact-list svg { width: 16px; height: 16px; margin-right: 10px; flex: none; }

  .address { position: absolute; left: 348px; top: 286px; font-size: 19px; line-height: 25px; color: var(--muted); }

  .services { position: absolute; left: 43px; top: 51px; color: var(--paper); }
  .services__heading { font-size: 21px; font-weight: 700; margin-bottom: 6px; }
  .services__list { list-style: none; }
  .services__list li { font-size: 20px; line-height: 26.5px; display: flex; align-items: center; }
  .services__list li::before { content: ""; width: 8px; height: 8px; border-radius: 50%; background: var(--paper);
                               margin: 0 10px 0 4px; }
</style>
</head>
<body>

<section class="card card--front" aria-label="Card front">
  <svg class="card__bands" width="689" height="394" aria-hidden="true">
    <rect x="0" y="117" width="689" height="7" fill="#000"/>
    <rect x="0" y="129" width="689" height="3" fill="#000"/>
    <rect x="0" y="254" width="689" height="4" fill="#000"/>
    <rect x="0" y="264" width="689" height="7" fill="#000"/>
  </svg>

  <div class="brand-seal">Vessolin<br>Hair Studio</div>

  <div class="stylist">
    <p class="stylist__name">MARCUS DELANE</p>
    <p class="stylist__title">Manager</p>
  </div>

  <ul class="contact-list">
    <li>
      <svg viewBox="0 0 16 16" aria-hidden="true"><path d="M3 1.5l3 .5 1 3.2-1.8 1.2a9 9 0 0 0 4.4 4.4L10.8 9l3.2 1 .5 3c-.2 1-1 1.6-2 1.5C6.8 14 2 9.2 1.5 3.5c-.1-1 .5-1.8 1.5-2z" fill="#000"/></svg>
      248-613-4087
    </li>
    <li>
      <svg viewBox="0 0 16 16" aria-hidden="true"><rect x="1.5" y="1.5" width="13" height="13" rx="2" fill="none" stroke="#000" stroke-width="2"/></svg>
      @vessolinhairstudio
    </li>
    <li>
      <svg viewBox="0 0 16 16" aria-hidden="true" fill="none" stroke="#000" stroke-width="1.3"><circle cx="8" cy="8" r="6.8"/><ellipse cx="8" cy="8" rx="3" ry="6.8"/><path d="M1.2 8h13.6M2.2 4.6h11.6M2.2 11.4h11.6M8 1.2v13.6"/></svg>
      www.vessolinhairstudio.example
    </li>
  </ul>

  <p class="address">41782 Pelham Crest Rd<br>Farmington MI</p>
</section>

<section class="card card--back" aria-label="Card back">
  <div class="services">
    <h2 class="services__heading">OUR SERVICES</h2>
    <ul class="services__list">
      <li>Custom Haircuts</li>
      <li>Coloring</li>
      <li>Extensions</li>
      <li>And Barbering</li>
      <li>Beard Grooming</li>
    </ul>
  </div>

  <div class="brand-seal">Vessolin<br>Hair Studio</div>
</section>

</body>
</html>
```